TL - business card

Tallow Partners is an insurance brokerage firm, inovative, proactive, vigorous, which aims to become the leader of the insurance brokers in Anfrica. We should like to get some designs which should be avoided also in Gray / Metallic for the Administration and Orange / Blue for the Managers (ike in the picture sent). The Blue / Green logo is not the correct one, but the source of the file. Please adjust the color accordingly for the business cards. 1 / Orange / Blue 2 / Gray / Metallic We want something classic but which is transmitted strenght, inovation, modernity and most of all, rapidity. We want something start-up like, very punchy and catching eye remaining profesional at the same time. Name: Dorian Whitlock Function: Managing Director Address: N ° 17/18 Rua Veloso - R / C 2B Direita - Bairro Mutamba - Luanda Tel: (+244) 947 582 316 Email: dorian.whitlock@tallow-p.example Website: www.tallow-p. example We want classic in the front and creative, colorfull at the back. The cards will be printed in relief, with very high quality of paper.
Insurance Broker
Colors
Designer to choose colors to be used in the design.

```html
<!DOCTYPE html>
<html lang="en">
<head>
<meta charset="utf-8">
<title>Tallow Partners – Business Card</title>
<link href="https://fonts.googleapis.com/css2?family=Roboto:wght@400;500;700&display=swap" rel="stylesheet">
<style>
  :root {
    --bg: #d9d9d9;
    --card-dark: #1c1d1f;
    --card-light: #ffffff;
    --green: #0d9444;
    --blue: #2ba3dc;
    --ink-light: #f2f2f2;
    --ink-dark: #3a3a3a;
    --divider: #8a8a8a;
  }
  * { box-sizing: border-box; margin: 0; padding: 0; }
  html, body { width: 1200px; height: 801px; overflow: hidden; }
  body {
    background: var(--bg);
    font-family: "Roboto", Arial, sans-serif;
    display: flex;
    align-items: center;
    justify-content: center;
    gap: 48px;
  }
  .card {
    width: 525px;
    height: 300px;
    position: relative;
    border-bottom: 4px solid var(--green);
    box-shadow: 0 10px 24px rgba(0,0,0,.22);
  }

  /* Back side */
  .card--back {
    background: var(--card-dark);
    display: flex;
    align-items: center;
    padding: 0 30px;
  }
  .brand-block {
    width: 200px;
    display: flex;
    flex-direction: column;
    align-items: center;
    gap: 14px;
  }
  .brand-mark {
    width: 58px; height: 58px;
    border-radius: 50%;
    border: 5px solid var(--green);
  }
  .brand-name {
    font-weight: 700;
    font-size: 20px;
    letter-spacing: .5px;
    text-transform: uppercase;
    color: var(--green);
    text-align: center;
  }
  .divider {
    width: 1px;
    height: 190px;
    background: linear-gradient(to bottom, transparent, var(--divider), transparent);
    margin: 0 24px;
  }
  .contact { color: var(--ink-light); font-size: 12.5px; line-height: 1.45; }
  .contact__name { color: var(--green); font-weight: 700; font-size: 21px; line-height: 1.1; }
  .contact__role { color: var(--blue); font-weight: 500; font-size: 13px; margin-bottom: 10px; }
  .contact__address { margin-bottom: 10px; }
  .contact__row { display: flex; align-items: center; gap: 8px; }
  .contact__row svg { width: 11px; height: 11px; flex: none; }

  /* Front side */
  .card--front {
    background: var(--card-light);
    display: flex;
    flex-direction: column;
    align-items: center;
    justify-content: center;
  }
  .card--front .brand-mark { width: 82px; height: 82px; border-width: 6px; margin-bottom: 14px; }
  .card--front .brand-name { font-size: 31px; }
  .website {
    margin-top: 42px;
    font-size: 14px;
    letter-spacing: 7px;
    color: var(--ink-dark);
  }
</style>
</head>
<body>
  <section class="card card--back">
    <div class="brand-block">
      <div class="brand-mark"></div>
      <div class="brand-name">Tallow Partners</div>
    </div>
    <div class="divider"></div>
    <div class="contact">
      <div class="contact__name">Dorian Whitlock</div>
      <div class="contact__role">Managing Director</div>
      <div class="contact__address">
        N ° 17/18 Rua Veloso<br>
        R / C 2B Direita<br>
        Bairro Mutamba, Luanda
      </div>
      <div class="contact__row">
        <svg viewBox="0 0 24 24" fill="var(--green)"><path d="M6.6 10.8a15 15 0 0 0 6.6 6.6l2.2-2.2c.3-.3.7-.4 1-.2 1.1.4 2.3.6 3.6.6.6 0 1 .4 1 1V20c0 .6-.4 1-1 1A17 17 0 0 1 3 4c0-.6.4-1 1-1h3.5c.6 0 1 .4 1 1 0 1.3.2 2.5.6 3.6.1.3 0 .7-.2 1z"/></svg>
        (+244) 947 582 316
      </div>
      <div class="contact__row">
        <svg viewBox="0 0 24 24" fill="var(--green)"><path d="M2 5h20v14H2z M2 5l10 8 10-8" stroke="var(--card-dark)" stroke-width="1.5"/></svg>
        dorian.whitlock@tallow-p.example
      </div>
      <div class="contact__row">
        <svg viewBox="0 0 24 24"><circle cx="12" cy="12" r="10" fill="var(--green)"/><path d="M2 12h20M12 2c3 3 3 17 0 20M12 2c-3 3-3 17 0 20" stroke="var(--card-dark)" stroke-width="1.3" fill="none"/></svg>
        www.tallow-p. example
      </div>
    </div>
  </section>

  <section class="card card--front">
    <div class="brand-mark"></div>
    <div class="brand-name">Tallow Partners</div>
    <div class="website">www.tallow-p. example</div>
  </section>
</body>
</html>
```